ORLA - Óptica Médica - web design and concept

Website concept - Create and develop our website design and structure. ORLA is an optical store chain, and we are looking to establish our web and digital concept. In attachment there are several pictures about our stores and our logo.

The website structure should be user friendly. Colors should be light and the design as simple and minimalist as possible. There are different variations of the logothat can be used, check the file.

The website will include optical collections and sun collections as an online store. Also, a medical menu should be considered in order for clients to schedule optometry appointments. There should also be a menu for client assistance where the clients can read about glass maintenance in our workshop.
Updates

Low design quality

Number of Pages Required

5+ page

Font styles to use
Serif
Sans Serif

Requirements
Must have
• Must be user-friendly and minimalist.
• Please USE PICTURES FROM THE BRANDS we sell: MERUN, BOSKA, PNW, KOLE, BAMPE
Nice to have
• Nice to inspire: ZEK glasses (see website https://ch.shopzek.com/en/)
• Nice to inspire: https://merun-eyewear.com/
• Nice to ispire: https://www.pnwglobe.com/en/
Should not have
• Hysteric colors and shapes

```html
<!DOCTYPE html>
<html lang="en">
<head>
<meta charset="utf-8">
<title>ORLA Óptica Médica</title>
<link href="https://fonts.googleapis.com/css2?family=Cormorant+Garamond:wght@500;600;700&family=Roboto:wght@400;500;700&display=swap" rel="stylesheet">
<style>
:root{
  --gold:#b08d57;
  --gold-dark:#9a7845;
  --ink:#1f1f1f;
  --text:#555;
  --muted:#888;
  --line:#e3e3e3;
  --cream:#fcf7ef;
  --footer:#1d1d1d;
  --footer-text:#bdbdbd;
  --white:#fff;
  --price:#c0392b;
}
*{box-sizing:border-box;margin:0;padding:0}
html,body{width:1200px;height:5248px;overflow:hidden}
body{position:relative;background:var(--white);font-family:'Roboto',Arial,sans-serif;color:var(--text);font-size:14px;line-height:1.7}
.abs{position:absolute}
.serif{font-family:'Cormorant Garamond',Georgia,serif}
.section-title{position:absolute;left:0;width:1200px;text-align:center;font-family:'Cormorant Garamond',Georgia,serif;font-weight:600;font-size:44px;letter-spacing:1px;color:var(--ink)}
.btn{position:absolute;display:flex;align-items:center;justify-content:center;background:var(--gold);color:var(--white);border-radius:20px;font-size:13px;font-weight:500}
.btn-outline{position:absolute;display:flex;align-items:center;justify-content:center;border:1px solid var(--gold);color:var(--gold);font-size:12px;letter-spacing:1px;background:var(--white)}
.photo{position:absolute}

/* header */
.site-header{position:absolute;top:0;left:0;width:1200px;height:88px;background:var(--white)}
.brand{position:absolute;left:88px;top:22px;display:flex;align-items:center;gap:10px;font-family:'Cormorant Garamond',Georgia,serif;font-weight:600;font-size:28px;color:var(--ink);letter-spacing:3px}
.brand i{display:block;width:12px;height:12px;background:var(--gold);border-radius:50%}
.nav{position:absolute;left:362px;top:34px;display:flex;gap:34px;font-size:14px;font-weight:500;color:var(--ink)}

/* hero */
.hero-title{left:100px;top:222px;font-size:48px;font-weight:600;color:var(--white);letter-spacing:1px}
.hero-sub{left:100px;top:290px;width:460px;font-size:18px;color:var(--white);line-height:1.5}
.dots{position:absolute;display:flex;gap:6px}
.dots span{width:10px;height:10px;border-radius:50%;border:1px solid #999;background:var(--white)}
.dots span.on{background:#999}

/* about */
.about-title{left:608px;top:640px;font-size:44px;font-weight:600;color:var(--ink)}
.about-text{left:608px;top:718px;width:492px;font-size:13px;line-height:2}

/* products */
.product-name{left:100px;top:1412px;font-size:20px;font-weight:700;color:var(--ink)}
.product-text{left:100px;top:1458px;width:460px;font-size:13px;line-height:2}
.stars{left:100px;top:1612px;color:var(--price);font-size:14px;letter-spacing:1px}
.price{left:100px;top:1640px;color:var(--price);font-size:17px}
.card-shadow{box-shadow:0 6px 18px rgba(0,0,0,.12);background:var(--white)}

/* arrivals */
.arrival-label{position:absolute;width:300px;text-align:center;font-size:20px;font-weight:500;color:var(--ink)}

/* features */
.feature-title{position:absolute;width:600px;text-align:center;font-size:28px;font-weight:500;color:var(--ink)}
.feature-text{position:absolute;width:380px;text-align:center;font-size:13px;line-height:2}

/* guarantees */
.guarantees{position:absolute;top:3268px;left:0;width:1200px;height:470px;background:var(--cream)}
.g-item{position:absolute;top:3476px;width:280px}
.g-item h3{font-size:21px;font-weight:500;color:var(--ink);line-height:1.35;margin-left:72px}
.g-item p{font-size:14px;line-height:2.3;margin-left:72px;margin-top:14px;color:#444}
.g-item svg{position:absolute;left:0;top:0}

/* brands */
.brand-mark{position:absolute;top:3942px;width:190px;text-align:center;color:#8a8a8a;font-family:'Cormorant Garamond',Georgia,serif;font-weight:600;font-size:24px;letter-spacing:2px}

/* blog */
.blog-card{position:absolute;top:4284px;width:280px;height:380px;background:var(--white);box-shadow:0 6px 18px rgba(0,0,0,.15)}
.blog-card .thumb{position:absolute;left:0;top:0;width:280px;height:170px}
.blog-card p{position:absolute;left:30px;top:205px;width:220px;text-align:center;font-size:14px;line-height:1.9;color:#444}
.blog-card .meta{position:absolute;left:0;top:320px;width:280px;text-align:center;font-size:12px;color:var(--gold)}

/* footer */
.site-footer{position:absolute;left:0;top:4776px;width:1200px;height:472px;background:var(--footer);color:var(--footer-text)}
.f-col{position:absolute;top:60px}
.f-col h4{font-family:'Cormorant Garamond',Georgia,serif;font-size:22px;font-weight:600;color:var(--white);margin-bottom:24px}
.f-col p,.f-col li{font-size:12px;line-height:2.4}
.f-col ul{list-style:none}
.f-row{display:flex;gap:10px;align-items:flex-start}
.copyright{position:absolute;left:0;top:440px;width:1200px;text-align:center;font-size:11px;color:#999}
</style>
</head>
<body>

<header class="site-header">
  <div class="brand"><i></i>ORLA</div>
  <nav class="nav"><span>Home</span><span>About Us</span><span>Products</span><span>Contact</span><span>Blog</span><span>Store</span></nav>
  <svg class="abs" style="left:822px;top:36px" width="18" height="18" viewBox="0 0 18 18"><circle cx="7.5" cy="7.5" r="5.5" fill="none" stroke="#222" stroke-width="2"/><line x1="11.5" y1="11.5" x2="16" y2="16" stroke="#222" stroke-width="2"/></svg>
  <svg class="abs" style="left:872px;top:36px" width="20" height="18" viewBox="0 0 20 18"><path d="M1 2h3l2.5 9h10l2-7H5" fill="none" stroke="#222" stroke-width="2"/><circle cx="8" cy="15" r="1.6" fill="#222"/><circle cx="15" cy="15" r="1.6" fill="#222"/></svg>
  <div class="btn" style="left:946px;top:28px;width:148px;height:36px">Get Free Trial</div>
</header>

<section>
  <div class="photo" role="img" aria-label="Smiling woman in sunglasses on a sunny city street" style="left:0;top:88px;width:1200px;height:466px;background:linear-gradient(90deg,#8a8478 0%,#b9ad9b 45%,#d9cbb6 70%,#c6b7a5 100%)"></div>
  <div class="abs serif hero-title">ORLA OPTICA MEDICA</div>
  <p class="abs hero-sub">We will be happy to help you and offer you the best solution for your visual health problems</p>
  <div class="btn" style="left:100px;top:394px;width:164px;height:46px;font-size:17px;border-radius:23px">Contact Us</div>
  <div class="dots" style="left:571px;top:516px"><span class="on"></span><span></span><span></span><span></span></div>
</section>

<section>
  <div class="photo" role="img" aria-label="Interior of the optical store with displays and chandelier" style="left:100px;top:658px;width:428px;height:568px;background:linear-gradient(180deg,#3a332c 0%,#6d5c49 45%,#b7aea4 75%,#d8d4ce 100%)"></div>
  <div class="abs serif about-title">ABOUT US</div>
  <p class="abs about-text">Lorem ipsum dolor sit amet, consectetur adipiscing elit, sed do eiusmod tempor incididunt ut labore et dolore magna aliqua. Ut enim ad minim veniam, quis nostrud exercitation ullamco laboris nisi ut aliquip ex ea commodo consequat. Duis aute irure dolor in reprehenderit in voluptate velit esse cillum dolore eu fugiat nulla pariatur.</p>
  <div class="btn" style="left:608px;top:922px;width:132px;height:36px;font-size:12px">READ MORE</div>
  <div class="photo" role="img" aria-label="Two friends laughing in sunglasses" style="left:550px;top:1022px;width:272px;height:204px;background:linear-gradient(135deg,#e0a45a,#c87a3a 55%,#3d6c8c)"></div>
  <div class="photo" role="img" aria-label="Open contact lens case" style="left:844px;top:1022px;width:256px;height:204px;background:linear-gradient(135deg,#f1f4f3,#cfe3dd 55%,#3fb7a1)"></div>
</section>

<section>
  <h2 class="section-title" style="top:1310px">PRODUCTS</h2>
  <div class="abs product-name">SUN GLASSES</div>
  <p class="abs product-text">Protect yourself adequately from ultraviolet (UV) rays thanks to our wide range of glasses, photochromic lenses and polarized lenses. Dress your look with the best quality and with prestigious brands: Hadrin Lowe, Benno Carrick, Ardent, Lumiva, Sorveta...</p>
  <div class="abs stars">★★★★★</div>
  <div class="abs price">£349.00</div>
  <div class="btn" style="left:100px;top:1684px;width:104px;height:34px;border-radius:2px;font-size:13px">Add To Cart</div>
  <div class="abs" style="left:234px;top:1684px;width:112px;height:34px;background:#eee;display:flex;align-items:center;justify-content:center;font-size:13px;color:#333">Buy Now</div>
  <div class="abs card-shadow" style="left:624px;top:1410px;width:476px;height:320px"></div>
  <div class="photo" role="img" aria-label="Mirrored sunglasses lying on sand" style="left:640px;top:1426px;width:444px;height:288px;background:linear-gradient(160deg,#c9b49a,#a8917a 50%,#8c7561)"></div>
  <div class="dots" style="left:580px;top:1768px"><span class="on"></span><span></span><span></span></div>
</section>

<section>
  <h2 class="section-title" style="top:1866px">NEW ARRIVALS</h2>
  <svg class="abs" style="left:42px;top:2046px" width="16" height="28" viewBox="0 0 16 28"><path d="M13 2L3 14l10 12" fill="none" stroke="#aaa" stroke-width="2"/></svg>
  <svg class="abs" style="left:1142px;top:2046px" width="16" height="28" viewBox="0 0 16 28"><path d="M3 2l10 12L3 26" fill="none" stroke="#aaa" stroke-width="2"/></svg>
  <div class="photo" role="img" aria-label="Black sunglasses, front view" style="left:80px;top:2000px;width:290px;height:140px;background:radial-gradient(ellipse at center,#3a3a3a 0%,#8c8c8c 45%,#fff 72%)"></div>
  <div class="photo" role="img" aria-label="Tortoiseshell sunglasses, front view" style="left:440px;top:2000px;width:290px;height:140px;background:radial-gradient(ellipse at center,#3b2a20 0%,#8f7a6b 45%,#fff 72%)"></div>
  <div class="photo" role="img" aria-label="Brown sunglasses, front view" style="left:800px;top:2000px;width:320px;height:140px;background:radial-gradient(ellipse at center,#4a2e22 0%,#9a8276 45%,#fff 72%)"></div>
  <svg class="abs" style="left:374px;top:1982px" width="20" height="18" viewBox="0 0 20 18"><path d="M10 16S2 11 2 6a4 4 0 018-1 4 4 0 018 1c0 5-8 10-8 10z" fill="none" stroke="#333" stroke-width="1.6"/></svg>
  <svg class="abs" style="left:728px;top:1982px" width="20" height="18" viewBox="0 0 20 18"><path d="M10 16S2 11 2 6a4 4 0 018-1 4 4 0 018 1c0 5-8 10-8 10z" fill="none" stroke="#333" stroke-width="1.6"/></svg>
  <svg class="abs" style="left:1082px;top:1982px" width="20" height="18" viewBox="0 0 20 18"><path d="M10 16S2 11 2 6a4 4 0 018-1 4 4 0 018 1c0 5-8 10-8 10z" fill="none" stroke="#333" stroke-width="1.6"/></svg>
  <div class="arrival-label" style="left:75px;top:2148px">PERSPICIATIS</div>
  <div class="arrival-label" style="left:435px;top:2148px">PERSPICIATIS</div>
  <div class="arrival-label" style="left:808px;top:2148px">PERSPICIATIS</div>
</section>

<section>
  <div class="photo" role="img" aria-label="Laughing couple wearing sunglasses at the beach" style="left:0;top:2286px;width:600px;height:490px;background:linear-gradient(135deg,#e7ddd0,#c79b73 45%,#6a8aa0)"></div>
  <div class="feature-title" style="left:600px;top:2400px">Man and Women Glasses</div>
  <p class="feature-text" style="left:710px;top:2466px">Sed ut perspiciatis unde omnis iste natus error sit voluptatem accusantium doloremque laudantium, totam rem aperiam, eaque ipsa quae ab illo inventore veritatis et quasi architecto.</p>
  <div class="btn-outline" style="left:818px;top:2600px;width:126px;height:40px">SHOP NOW</div>

  <div class="feature-title" style="left:0;top:2890px">Collection of sunglasses</div>
  <p class="feature-text" style="left:110px;top:2956px">Sed ut perspiciatis unde omnis iste natus error sit voluptatem accusantium doloremque laudantium, totam rem aperiam, eaque ipsa quae ab illo inventore veritatis et quasi architecto.</p>
  <div class="btn-outline" style="left:252px;top:3090px;width:126px;height:40px">SHOP NOW</div>
  <div class="photo" role="img" aria-label="Woman in sunglasses sitting among green trees" style="left:600px;top:2776px;width:600px;height:490px;background:linear-gradient(135deg,#3f6d2e,#7ea24c 45%,#c9b98c 80%)"></div>
</section>

<section>
  <div class="guarantees"></div>
  <h2 class="section-title" style="top:3350px">OUR GUARANTEES</h2>
  <svg class="abs" style="left:40px;top:3488px" width="14" height="22" viewBox="0 0 14 22"><path d="M12 2L3 11l9 9" fill="none" stroke="#111" stroke-width="3"/></svg>
  <svg class="abs" style="left:1146px;top:3488px" width="14" height="22" viewBox="0 0 14 22"><path d="M2 2l9 9-9 9" fill="none" stroke="#111" stroke-width="3"/></svg>
  <div class="g-item" style="left:116px">
    <svg width="34" height="40" viewBox="0 0 34 40"><circle cx="17" cy="8" r="6" fill="none" stroke="#b08d57" stroke-width="2"/><path d="M7 38V22a10 10 0 0120 0v16" fill="none" stroke="#b08d57" stroke-width="2"/></svg>
    <h3>Orla Childhood Guarantee</h3>
    <p>50% discount on new glasses, if your child's graduation has changed before six months.</p>
  </div>
  <div class="g-item" style="left:444px">
    <svg width="44" height="30" viewBox="0 0 44 30"><rect x="2" y="6" width="26" height="18" fill="none" stroke="#b08d57" stroke-width="2"/><path d="M28 12h8l6 6v6H28z" fill="none" stroke="#b08d57" stroke-width="2"/><circle cx="10" cy="26" r="3" fill="#b08d57"/><circle cx="34" cy="26" r="3" fill="#b08d57"/></svg>
    <h3>Orla Accident Warranty</h3>
    <p>Did you get off your glasses when you got out of the car? Did your little boy play with his sunglasses?</p>
  </div>
  <div class="g-item" style="left:772px">
    <svg width="36" height="36" viewBox="0 0 36 36"><circle cx="18" cy="10" r="6" fill="none" stroke="#b08d57" stroke-width="2"/><path d="M6 34c0-8 5-13 12-13s12 5 12 13" fill="none" stroke="#b08d57" stroke-width="2"/></svg>
    <h3>Orla Security</h3>
    <p>If you have suffered a robbery or robbery in your home, you will opt for the replacement of the same product at half price.</p>
  </div>
</section>

<section>
  <h2 class="section-title" style="top:3820px">OUR BRANDS</h2>
  <div class="brand-mark" style="left:76px">MARISA VELDEN</div>
  <div class="brand-mark" style="left:296px">LURANO</div>
  <div class="brand-mark" style="left:508px">PELLA VOSS</div>
  <div class="brand-mark" style="left:722px">ARDENT</div>
  <div class="brand-mark" style="left:936px">SORVETA</div>
</section>

<section>
  <h2 class="section-title" style="top:4180px">LATEST BLOG</h2>
  <article class="blog-card" style="left:100px">
    <div class="thumb" role="img" aria-label="Optician with glasses beside an article headline about eyelid care" style="background:linear-gradient(135deg,#5a6470,#c9c2b8 60%,#e8b04a)"></div>
    <p>Lorem ipsum dolor sit amet, consectetur adipiscing elit, sed do eiusmod tempor incididunt</p>
    <div class="meta">◷ 10 &nbsp; ◷ March 2,2017</div>
  </article>
  <article class="blog-card" style="left:460px">
    <div class="thumb" role="img" aria-label="Optician beside an article headline about children's sunglasses" style="background:linear-gradient(135deg,#3a4aa8,#d24fb0 55%,#f2d14a)"></div>
    <p>Lorem ipsum dolor sit amet, consectetur adipiscing elit, sed do eiusmod tempor incididunt</p>
    <div class="meta">◷ 10 &nbsp; ◷ March 2,2017</div>
  </article>
  <article class="blog-card" style="left:822px">
    <div class="thumb" role="img" aria-label="Optician beside an article headline about sun protection" style="background:linear-gradient(135deg,#4a4f5a,#e0c840 55%,#d84a8a)"></div>
    <p>Lorem ipsum dolor sit amet, consectetur adipiscing elit, sed do eiusmod tempor incididunt</p>
    <div class="meta">◷ 10 &nbsp; ◷ March 2,2017</div>
  </article>
</section>

<footer class="site-footer">
  <div class="f-col" style="left:100px;width:220px">
    <h4>Who We Are</h4>
    <p>ORLA OPTICA opens its doors with a clear purpose: to take care of you. Our priority is your visual health, and for this reason we have the best professionals and the most competitive products to serve your needs.</p>
    <div class="btn" style="position:relative;margin-top:30px;width:190px;height:40px;font-size:11px">BOOK AN APPOINTMENT</div>
  </div>
  <div class="f-col" style="left:385px;width:230px">
    <h4>Contact Details</h4>
    <div class="f-row"><svg width="12" height="16" viewBox="0 0 12 16" style="margin-top:8px"><path d="M6 15S1 9 1 6a5 5 0 0110 0c0 3-5 9-5 9z" fill="#b08d57"/><circle cx="6" cy="6" r="2" fill="#1d1d1d"/></svg><p>Address Calle Almendros, 22, Norvalle</p></div>
    <div class="f-row"><svg width="12" height="14" viewBox="0 0 12 14" style="margin-top:9px"><path d="M2 1h3l1 3-2 1a7 7 0 003 4l1-2 3 1v3c0 1-1 2-2 2A10 10 0 011 3c0-1 0-2 1-2z" fill="#b08d57"/></svg><p>Telephone 900 41 27 63</p></div>
    <div class="f-row"><svg width="14" height="12" viewBox="0 0 14 12" style="margin-top:10px"><rect x="1" y="1" width="12" height="10" fill="none" stroke="#b08d57" stroke-width="1.5"/><path d="M1 1l6 5 6-5" fill="none" stroke="#b08d57" stroke-width="1.5"/></svg><p>orlaoptica@example.com</p></div>
  </div>
  <div class="f-col" style="left:680px;width:220px">
    <h4>Opening Hours</h4>
    <div class="f-row"><svg width="14" height="14" viewBox="0 0 14 14" style="margin-top:8px"><circle cx="7" cy="7" r="6" fill="#b08d57"/><path d="M7 3v4h3" fill="none" stroke="#1d1d1d" stroke-width="1.5"/></svg><p>Monday - Friday: 10:00 - 14:00 &amp;<br>17:00 - 20:30<br>Saturday: 10:00 - 14:00</p></div>
  </div>
  <div class="f-col" style="left:955px;width:160px">
    <h4>Quick Links</h4>
    <ul>
      <li>› &nbsp;Home</li><li>› &nbsp;About Us</li><li>› &nbsp;Products</li><li>› &nbsp;Contact</li><li>› &nbsp;Blog</li><li>› &nbsp;Store</li>
    </ul>
  </div>
  <div class="copyright">© Copyrights 2018 Orlaoptica All Rights Reserved</div>
</footer>

</body>
</html>
```